Wireless Internet Service Provider website design

We need a Internet Service Provider website that show the packages that we offer as well as the functionality where customers have the option of clicking on the various packages and be linked to a page where they can sign up for our services.
We need about 10-15 pages.
A. Integrated online store.
B. Live chat.
C. Social media page
My old website. Brightlinkradio.nyc

Example: http://plumcrestnet.com/services/residential/ Added Tuesday, June 7, 2016

Target Market(s)

Residential and small businesses

Industry/Entity Type

Internet

Coding

Coded - Design and coding required

Number of Pages Required

5+ page

Font styles to use
Serif
Sans Serif
Script

Colors
3176b5
85cae6
ffffff

Requirements
Must have
• Online store and live chat, drop down details on pricing from current website
Nice to have
• great design, functional website,

```html
<!DOCTYPE html>
<html lang="en">
<head>
<meta charset="utf-8">
<title>Swiftpath Wireless</title>
<link href="https://fonts.googleapis.com/css2?family=Raleway:wght@400;500;600&family=Open+Sans:wght@400;600&display=swap" rel="stylesheet">
<style>
:root{
  --blue:#0b5a99;
  --blue-dark:#084a80;
  --sky:#29b6e0;
  --ink:#333;
  --muted:#666;
  --grey-band:#e1e1e1;
  --card-grey:#b5b5b5;
  --price-bg:#f1f1f1;
  --footer-dark:#2f2f2f;
  --white:#fff;
}
*{box-sizing:border-box;margin:0;padding:0}
html,body{width:1200px;height:2514px;overflow:hidden}
body{font-family:"Open Sans",Arial,sans-serif;color:var(--ink);background:var(--white);position:relative}
.wrap{width:1002px;margin:0 auto;position:relative}
h1,h2,h3,.raleway{font-family:"Raleway",Arial,sans-serif;font-weight:500}

/* header */
.site-header{height:64px;border-top:3px solid var(--blue);border-bottom:1px solid #ddd;position:relative}
.brand{position:absolute;left:99px;top:14px;display:flex;align-items:center;gap:10px;font-family:"Raleway",sans-serif;font-weight:600;font-size:28px;color:var(--blue)}
.brand .mark{width:26px;height:26px;border-radius:50%;background:var(--sky)}
.main-nav{position:absolute;right:220px;top:22px;display:flex;gap:27px;font-size:12.5px;color:#444}
.main-nav .active{color:var(--blue)}
.search-btn{position:absolute;left:1056px;top:15px;width:45px;height:33px;background:var(--blue);border-radius:2px;display:flex;align-items:center;justify-content:center}

/* hero */
.hero{height:409px;position:relative;background:linear-gradient(100deg,#5d6b76 0%,#7e8d98 30%,#2f5f7a 60%,#1d4e6a 100%)}
.hero .arrow{position:absolute;top:185px}
.live-chat{position:absolute;right:0;bottom:2px;width:133px;height:36px;background:var(--sky);color:#fff;font-family:"Raleway",sans-serif;font-size:18px;display:flex;align-items:center;justify-content:center;gap:8px}

/* welcome */
.welcome{height:365px;text-align:center;padding-top:42px}
.welcome h1{font-size:26px;color:#222}
.welcome h1 span{color:var(--blue)}
.welcome .lede{font-family:"Raleway",sans-serif;font-size:16.5px;color:#777;margin-top:16px}
.rule{width:206px;height:2px;background:var(--blue);margin:18px auto 0}
.welcome p.body{font-size:11.3px;line-height:28px;color:#555;width:870px;margin:20px auto 0}
.actions{display:flex;justify-content:center;gap:38px;margin-top:40px}
.btn{width:173px;height:45px;display:flex;align-items:center;justify-content:center;font-family:"Raleway",sans-serif;font-size:17px;color:#fff;border-radius:2px}
.btn-dark{background:linear-gradient(#4a4a4a,#262626)}
.btn-blue{background:linear-gradient(#1570b8,#0a5493);width:178px}

/* services */
.services{height:328px;background:var(--grey-band);border-bottom:1px solid #ccc;padding-top:39px}
.services .wrap{display:flex;justify-content:space-between}
.service{width:312px;height:256px;border:3px solid #fff;position:relative;box-shadow:0 1px 3px rgba(0,0,0,.2)}
.service .photo{position:absolute;inset:0}
.service .label{position:absolute;left:0;right:0;bottom:0;height:42px;background:rgba(30,30,30,.75);color:#fff;font-family:"Raleway",sans-serif;font-size:15px;display:flex;align-items:center;justify-content:center}

/* packages */
.packages{height:663px;padding-top:52px;text-align:center}
.packages h2{font-size:25px;color:var(--blue)}
.packages .rule{width:160px;margin-top:20px}
.plans{display:flex;justify-content:space-between;margin-top:44px;text-align:left}
.plan{width:322px;height:454px;background:var(--card-grey);border-radius:3px;padding:13px 13px 0;position:relative}
.plan.featured{background:var(--blue)}
.plan h3{text-align:center;font-size:26px;color:#333;margin-top:7px}
.plan .speed{text-align:center;font-size:13px;color:#333;margin-top:6px}
.plan.featured h3,.plan.featured .speed{color:#fff}
.plan .inner{position:absolute;left:13px;right:13px;top:92px;height:312px;background:#fff}
.plan .price{height:60px;background:var(--price-bg);display:flex;align-items:center;justify-content:center;font-family:"Raleway",sans-serif;font-size:27px;font-weight:500;color:var(--blue)}
.plan .desc{font-size:11.5px;line-height:23px;color:#444;padding:18px 22px 0}
.plan h4{font-family:"Raleway",sans-serif;font-weight:500;font-size:17px;color:var(--blue);padding:17px 22px 8px}
.plan ul{list-style:none;padding:0 22px}
.plan li{font-size:11.5px;color:#444;height:35px;display:flex;align-items:center;gap:18px}
.plan li::before{content:"\00BB";font-size:15px;color:#333}
.plan .signup{position:absolute;left:0;right:0;bottom:12px;text-align:center;font-size:13px;color:#333;text-decoration:underline}
.plan.featured .signup{color:#fff}

/* subscribe */
.subscribe{height:105px;background:linear-gradient(90deg,#1665a6,#1e74b6 50%,#1665a6);display:flex;align-items:center;justify-content:center;gap:21px}
.subscribe .field{width:520px;height:42px;border:1px solid #8fb9dc;color:#fff;font-size:13px;display:flex;align-items:center;padding-left:14px}
.subscribe .go{width:131px;height:42px;background:linear-gradient(#3d3d3d,#222);color:#fff;font-family:"Raleway",sans-serif;font-size:19px;display:flex;align-items:center;justify-content:center;border-radius:2px}

/* testimonials */
.testimonials{height:268px;padding-top:45px}
.test-head{display:flex;align-items:center;gap:20px;padding-left:20px}
.test-head h2{font-size:25px;color:var(--blue);white-space:nowrap}
.test-head .line{flex:1;height:1px;background:#ddd}
.test-head .nav{font-size:16px;color:#999}
.test-body{display:flex;margin-top:36px}
.avatar{width:230px;height:110px;position:relative;flex:none}
.avatar .quote{position:absolute;left:0;top:0;width:110px;height:110px;border-radius:50%;background:#888;display:flex;align-items:center;padding-left:20px}
.avatar .photo{position:absolute;left:58px;top:-6px;width:120px;height:120px;border-radius:50%;border:4px solid #fff;background:radial-gradient(circle at 50% 40%,#e7d6cc,#bfb2ab)}
.test-body .words{flex:1;padding-left:0}
.test-body p{font-size:11.3px;line-height:25px;color:#555}
.test-body .author{font-family:"Raleway",sans-serif;font-size:15px;color:var(--blue);margin-top:5px}
.divider{height:2px;background:var(--blue)}

/* footer */
.site-footer{height:237px;padding-top:35px}
.site-footer .wrap{display:flex}
.site-footer h5{font-family:"Raleway",sans-serif;font-weight:500;font-size:15px;color:#333;margin-bottom:18px}
.f-contact{width:250px;border-right:1px solid #ddd;height:150px}
.f-contact .row{display:flex;gap:14px;font-size:11.5px;line-height:22px;color:#444;margin-bottom:14px}
.f-contact svg{flex:none;margin-top:4px}
.f-terms{width:256px;padding-left:60px;border-right:1px solid #ddd;height:150px;margin-right:50px}
.f-terms li{list-style:none;font-size:11.5px;color:#444;height:27.5px}
.f-terms li::before{content:"\00BB";color:var(--blue);margin-right:10px}
.map{position:absolute;right:0;top:-10px;width:446px;height:166px;border:2px solid #9cc3e4;background:linear-gradient(135deg,#e8e4d8,#d9dde0 45%,#9fc4e6 70%,#e5e1d5)}
.bottom-bar{position:absolute;left:0;top:2439px;width:1200px;height:75px;background:var(--footer-dark);color:#fff;font-size:12px;display:flex;align-items:center;justify-content:center;gap:8px}
</style>
</head>
<body>

<header class="site-header">
  <div class="brand"><span class="mark"></span>Swiftpath Wireless</div>
  <nav class="main-nav">
    <span class="active">Home</span><span>Why Swiftpath</span><span>Plans &amp; Packages</span><span>My Account</span><span>Gallery</span><span>Contacts</span>
  </nav>
  <div class="search-btn">
    <svg width="18" height="18" viewBox="0 0 18 18"><circle cx="7.5" cy="7.5" r="5.5" fill="none" stroke="#fff" stroke-width="2.4"/><line x1="11.5" y1="11.5" x2="16" y2="16" stroke="#fff" stroke-width="2.6" stroke-linecap="round"/></svg>
  </div>
</header>

<section class="hero" role="img" aria-label="Hero photo: hands using devices with connected network icons in blue tones">
  <svg class="arrow" style="left:44px" width="18" height="32" viewBox="0 0 18 32"><polyline points="16,2 2,16 16,30" fill="none" stroke="#fff" stroke-width="2"/></svg>
  <svg class="arrow" style="right:44px" width="18" height="32" viewBox="0 0 18 32"><polyline points="2,2 16,16 2,30" fill="none" stroke="#fff" stroke-width="2"/></svg>
  <div class="live-chat">Live Chat
    <svg width="22" height="16" viewBox="0 0 22 16"><ellipse cx="8" cy="6.5" rx="8" ry="6" fill="#fff"/><ellipse cx="15" cy="9.5" rx="7" ry="5.5" fill="#fff" stroke="#29b6e0" stroke-width="1.2"/></svg>
  </div>
</section>

<section class="welcome">
  <h1>Welcome To <span>Swiftpath Wireless</span></h1>
  <p class="lede">Vel wisi dissentiet ana nam novum reformidansaltevivendum</p>
  <div class="rule"></div>
  <p class="body">Congue verterem periculis no vim. Ne usu eruditi utroque corpora, ut ferri deleniti laboramus vix. Eum ex agam labores cotidieque, pro eu vocent singulis. Idque affert dolorem nec id. Ei per civibus propriae assueverit. Id sed luptatum inimicus consequat, duo regione definiebas eu. Omnis meliore qui cu, ad possit nonumes feugait usu. Vix quas prompta perfecto id, nobis prompta sanctus pro no. Ei malorum pertinacia ius. At posse graece utamur duo.</p>
  <div class="actions">
    <span class="btn btn-dark">Read More Info</span>
    <span class="btn btn-blue">Quick Contact</span>
  </div>
</section>

<section class="services">
  <div class="wrap">
    <div class="service"><div class="photo" role="img" aria-label="Photo: person in suit holding connected devices" style="background:linear-gradient(160deg,#3b4a5c,#8fa6bd 55%,#2a3340)"></div><div class="label">Residential Internet Access</div></div>
    <div class="service"><div class="photo" role="img" aria-label="Photo: hands typing on a laptop keyboard" style="background:linear-gradient(160deg,#c9d6e2,#eef2f5 50%,#b5bcc3)"></div><div class="label">Business Internet Access</div></div>
    <div class="service"><div class="photo" role="img" aria-label="Photo: person using a tablet on a sofa" style="background:linear-gradient(160deg,#8a8a8a,#c4c4c4 50%,#5d6e86)"></div><div class="label">Unlimited Internet Usage</div></div>
  </div>
</section>

<section class="packages">
  <div class="wrap">
    <h2>Packages and Promotions</h2>
    <div class="rule"></div>
    <div class="plans">
      <div class="plan">
        <h3>Swiftpath Simplicity</h3>
        <div class="speed">5 Mbps Download Speed</div>
        <div class="inner">
          <div class="price">$39.99&nbsp; mo./1yr</div>
          <p class="desc">The right speed for occasional internet usage, including checking emails, social networks and light internet browsing.</p>
          <h4>Includes</h4>
          <ul><li>Free smart router</li><li>Free internet protection</li><li>Unlimited Swiftpath Wi-Fi access</li></ul>
        </div>
        <span class="signup">Sign up Now</span>
      </div>
      <div class="plan featured">
        <h3>Swiftpath Value Pak</h3>
        <div class="speed">10 Mbps Download Speed</div>
        <div class="inner">
          <div class="price">$49.95 mo/1yr</div>
          <p class="desc">Great for 2-5 devices online at the same time, read emails, browse social media and internet.</p>
          <h4>Includes</h4>
          <ul><li>Free smart router</li><li>Free internet protection</li><li>Unlimited Swiftpath Wi-Fi access</li></ul>
        </div>
        <span class="signup">Sign up Now</span>
      </div>
      <div class="plan">
        <h3>Swiftpath Super-Pak</h3>
        <div class="speed">25 Mbps Download Speed</div>
        <div class="inner">
          <div class="price">$ 69.99 mo/1yr</div>
          <p class="desc">With Swiftpath Super-Pak 25, you get speedy downloads of up to 25 Mbps. It's great for a busy household, especially if you streaming.</p>
          <h4>Includes</h4>
          <ul><li>Free smart router</li><li>Free internet protection</li><li>Unlimited Swiftpath Wi-Fi access</li></ul>
        </div>
        <span class="signup">Sign up Now</span>
      </div>
    </div>
  </div>
</section>

<section class="subscribe">
  <div class="field">Email</div>
  <div class="go">Subscribe</div>
</section>

<section class="testimonials">
  <div class="wrap">
    <div class="test-head"><h2>Our Testimonials</h2><span class="line"></span><span class="nav">&lsaquo; &rsaquo;</span></div>
    <div class="test-body">
      <div class="avatar">
        <div class="quote"><svg width="30" height="24" viewBox="0 0 30 24"><path d="M2 22V12C2 6 5 2 11 1v4c-3 1-4 3-4 6h4v11zM17 22V12c0-6 3-10 9-11v4c-3 1-4 3-4 6h4v11z" fill="#fff"/></svg></div>
        <div class="photo" role="img" aria-label="Portrait photo of a customer"></div>
      </div>
      <div class="words">
        <p>An vero utroque duo. Nam ea illum invenire, usu dicunt euismod maluisset ea. Homero laoreet in usu, utinam vocent bonorum mel ut. Summo tempor id vix, vis ad idque omittam lucilius. Mei ex insolens inimicus. In minim dolorem qualisque sea. An vero utroque duo. Nam ea illum invenire, usu dicunt euismod maluisset ea. Homero laoreet in usu, utinam vocent bonorum mel ut.</p>
        <div class="author">- Dicam mucius mandamus</div>
      </div>
    </div>
  </div>
</section>

<div class="wrap"><div class="divider"></div></div>

<footer class="site-footer">
  <div class="wrap">
    <div class="f-contact">
      <h5>CONTACT</h5>
      <div class="row"><svg width="16" height="14" viewBox="0 0 16 14"><path d="M8 0L0 7h2v7h4V9h4v5h4V7h2z" fill="#0b5a99"/></svg><span>2480 W. Harlow Ln. | Maplewood<br>KS 66000</span></div>
      <div class="row"><svg width="16" height="16" viewBox="0 0 16 16"><rect x="4" y="0" width="8" height="16" rx="1.5" fill="none" stroke="#0b5a99" stroke-width="1.6"/><circle cx="8" cy="13" r="1" fill="#0b5a99"/></svg><span>Call Us : (555)010-4821</span></div>
      <div class="row"><svg width="16" height="12" viewBox="0 0 16 12"><rect x="0.8" y="0.8" width="14.4" height="10.4" fill="none" stroke="#0b5a99" stroke-width="1.6"/><polyline points="1,1 8,7 15,1" fill="none" stroke="#0b5a99" stroke-width="1.6"/></svg><span>info@swiftpathwireless.example</span></div>
    </div>
    <div class="f-terms">
      <h5>TERMS</h5>
      <ul><li>Homero eleifend</li><li>Rationibus referrentur</li><li>Evertitur ad</li><li>Homero eleifend</li><li>An tota zril assuev</li></ul>
    </div>
    <div class="map" role="img" aria-label="Street map showing the office location"></div>
  </div>
</footer>

<div class="bottom-bar">
  <svg width="13" height="13" viewBox="0 0 13 13"><circle cx="6.5" cy="6.5" r="5.6" fill="none" stroke="#fff" stroke-width="1.4"/><path d="M8.6 4.6a2.6 2.6 0 1 0 0 3.8" fill="none" stroke="#fff" stroke-width="1.4"/></svg>
  <span>Companyname 2016 . All Rights Reserved . Privacypolicy</span>
</div>

</body>
</html>
```